New & Improved KIVORA Business Card

I would like a two sided business card one side dedicated to home automation (security camera installation, television & sound bar mounting (hidden wires optional) , sink installation, fireplace mounting, chandelier installation and one side dedicated to all electronic repairs, In ex: plume band repairs, computer, zTab, laptop repairs, Velofon's, Korvex and etc.. Using the colors on this flyer. The phone number &email I want on both sides is (555) 214-3907 & Tech@Kivora.help. SAME COLOR AS THE FLYER ATTACHED.

Target Market(s)

EVERYONE.

Contact Information for Business Card

I would like a two sided business card one side dedicated to home automation (security camera installation, television & sound bar mounting (hidden wires optional) , sink installation, fireplace mounting, chandelier installation and one side dedicated to all electronic repairs, In ex: plume band repairs, computer, zTab, laptop repairs, Velofon's, Korvex and etc.. Using the colors on this flyer. The phone number &email I want on both sides is (555) 214-3907 & Tech@Kivora.help

Requirements
Must have
• -TV MOUNTING
-HOME AUTOMATION
-SECURITY CAMERA INSTALLATION
-ALL ELECTRONIC REPAIRS
- (555) 214-3907
-Tech@Kivora.help
-SAME COLOR AS THE FLYER
Nice to have
• Same colors & concept as the flyer attached below.
Should not have
• DO NOT DO A DIFF COLOR I WANT SAME COLOR AS THE FLYER ATTACHED.

```html
<!DOCTYPE html>
<html lang="en">
<head>
<meta charset="utf-8">
<title>KIVORA Business Card</title>
<link href="https://fonts.googleapis.com/css2?family=Montserrat:wght@500;700&family=Roboto:wght@400;500&display=swap" rel="stylesheet">
<style>
  :root {
    --page-bg: #4a4a4a;
    --card-bg: #333333;
    --card-shadow: rgba(0, 0, 0, 0.45);
    --logo-silver: #d9d9d9;
    --text-bright: #f2f2f2;
    --text-muted: #7a7a7a;
    --divider: #e6e6e6;
  }
  * { box-sizing: border-box; margin: 0; padding: 0; }
  html, body {
    width: 1200px;
    height: 1126px;
    overflow: hidden;
    background: var(--page-bg);
  }
  .sheet {
    position: relative;
    width: 1200px;
    height: 1126px;
  }
  .card {
    position: absolute;
    left: 250px;
    width: 700px;
    height: 400px;
    background: var(--card-bg);
    box-shadow: 0 10px 24px var(--card-shadow);
    display: flex;
    flex-direction: column;
    align-items: center;
    justify-content: center;
  }
  .card--services { top: 140px; }
  .card--contact { top: 586px; }

  .wordmark {
    font-family: "Montserrat", sans-serif;
    font-weight: 700;
    color: var(--logo-silver);
    letter-spacing: 0.22em;
    line-height: 1;
    padding-left: 0.22em;
  }
  .card--services .wordmark { font-size: 64px; margin-bottom: 44px; }
  .card--contact .wordmark { font-size: 84px; margin-bottom: 26px; }

  .service-list {
    list-style: none;
    font-family: "Montserrat", sans-serif;
    font-weight: 500;
    font-size: 17px;
    letter-spacing: 0.08em;
    color: var(--text-muted);
    text-align: left;
  }
  .service-list li { margin: 8px 0; white-space: nowrap; }
  .service-list .highlight { color: var(--text-bright); }
  .service-list .divider {
    display: inline-block;
    width: 2px;
    height: 14px;
    background: var(--divider);
    margin: 0 18px;
    vertical-align: -1px;
  }

  .contact-row {
    display: flex;
    align-items: center;
    gap: 40px;
    font-family: "Roboto", sans-serif;
    font-weight: 500;
    font-size: 21px;
    letter-spacing: 0.06em;
    color: var(--text-bright);
  }
  .contact-item { display: flex; align-items: center; gap: 12px; }
  .contact-item .muted { color: var(--text-muted); }
  .contact-icon { width: 22px; height: 22px; fill: var(--text-muted); }
</style>
</head>
<body>
<main class="sheet">
  <section class="card card--services" aria-label="Card side with services">
    <h1 class="wordmark">KIVORA</h1>
    <ul class="service-list">
      <li><span>TV </span><span class="highlight">MOUNTING</span><span class="divider"></span><span>SECURITY </span><span class="highlight">CAMERA INSTALLATION</span></li>
      <li><span>HOME </span><span class="highlight">AUTOMATION</span><span class="divider"></span><span>ALL </span><span class="highlight">ELECTRONIC REPAIRS</span></li>
    </ul>
  </section>

  <section class="card card--contact" aria-label="Card side with contact details">
    <h2 class="wordmark">KIVORA</h2>
    <div class="contact-row">
      <div class="contact-item">
        <svg class="contact-icon" viewBox="0 0 24 24" aria-hidden="true">
          <path d="M6.6 10.8c1.4 2.8 3.8 5.1 6.6 6.6l2.2-2.2c.3-.3.7-.4 1-.2 1.1.4 2.3.6 3.6.6.6 0 1 .4 1 1V20c0 .6-.4 1-1 1C10.6 21 3 13.4 3 4c0-.6.4-1 1-1h3.5c.6 0 1 .4 1 1 0 1.3.2 2.5.6 3.6.1.3 0 .7-.2 1L6.6 10.8z"/>
        </svg>
        <span><span class="muted">(555)</span> 214-3907</span>
      </div>
      <div class="contact-item">
        <svg class="contact-icon" viewBox="0 0 24 24" aria-hidden="true">
          <path d="M2 5h20v14H2z M3.5 6.5 12 13l8.5-6.5" fill="none" stroke="#7a7a7a" stroke-width="1.8"/>
        </svg>
        <span><span class="muted">Tech@</span>Kivora.help</span>
      </div>
    </div>
  </section>
</main>
</body>
</html>
```